Consumer and commercial IOT solutions (Internet Of Things)

We are a startup and are looking for business cards with logo. The logo will appear on all of our media as well as our ecommerce site and social sites that have yet to be developed. We want to present a fresh face on a high tech company that innovates at every turn. You can read about our solutions on our information only web site www.plonaxhub.net - We have some wording we would like used on our business cards but there is no place for this except for here. The company name is "RM Industrial IOT" I have some samples of logos I am interested in seeing but I will let your team make the initial presentations

```html
<!DOCTYPE html>
<html lang="en">
<head>
<meta charset="utf-8">
<title>RM Industrial IOT — Business Card</title>
<link href="https://fonts.googleapis.com/css2?family=Arimo:wght@400;700&display=swap" rel="stylesheet">
<style>
  :root {
    --backdrop: #3a3a3c;
    --card-navy: #0a1a5c;
    --ink-white: #ffffff;
    --ink-soft: #e6e9f5;
  }
  * { box-sizing: border-box; margin: 0; padding: 0; }
  html, body {
    width: 1200px; height: 1015px; overflow: hidden;
    background: var(--backdrop);
    font-family: "Arimo", Arial, sans-serif;
    color: var(--ink-white);
  }
  .stage {
    width: 1200px; height: 1015px;
    display: flex; flex-direction: column; align-items: center; justify-content: center; gap: 50px;
  }
  .card {
    position: relative; width: 630px; height: 360px;
    background: var(--card-navy);
    box-shadow: 0 10px 24px rgba(0,0,0,.45);
  }
  .card-front { display: flex; align-items: center; justify-content: center; gap: 30px; }
  .brand-dot {
    width: 116px; height: 116px; border-radius: 50%;
    border: 5px solid var(--ink-white); flex: none;
  }
  .brand-name {
    font-weight: 400; text-transform: uppercase; color: var(--ink-white);
    font-size: 36px; line-height: 1.15; letter-spacing: 1px;
  }
  .card-back { padding: 36px 44px; }
  .card-back .brand-name { font-size: 30px; }
  .person { margin-top: 24px; }
  .person-name { font-weight: 700; font-size: 25px; letter-spacing: .5px; text-transform: uppercase; line-height: 1.2; }
  .person-role { font-size: 17px; color: var(--ink-soft); margin-top: 2px; }
  .contact-list { list-style: none; margin-top: 14px; font-size: 17px; line-height: 1.45; }
  .contact-list li { display: flex; align-items: center; gap: 9px; }
  .contact-list svg { width: 17px; height: 17px; flex: none; }
  .address { margin-top: 12px; font-size: 17px; line-height: 1.35; }
</style>
</head>
<body>
<main class="stage">
  <section class="card card-front" aria-label="Card front">
    <div class="brand-dot"></div>
    <p class="brand-name">RM Industrial<br>IOT</p>
  </section>

  <section class="card card-back" aria-label="Card back">
    <p class="brand-name">RM Industrial<br>IOT</p>
    <div class="person">
      <p class="person-name">Daniel Foster</p>
      <p class="person-role">Managing Director</p>
    </div>
    <ul class="contact-list">
      <li><svg viewBox="0 0 24 24" fill="#fff"><path d="M6.6 10.8a15 15 0 0 0 6.6 6.6l2.2-2.2c.3-.3.7-.4 1-.2 1.1.4 2.3.6 3.6.6.6 0 1 .4 1 1V20c0 .6-.4 1-1 1A17 17 0 0 1 3 4c0-.6.4-1 1-1h3.5c.6 0 1 .4 1 1 0 1.3.2 2.5.6 3.6.1.3 0 .7-.2 1z"/></svg>052-418 730 264</li>
      <li><svg viewBox="0 0 24 24" fill="#fff"><path d="M2 5h20v14H2zm2 2v.5l8 5 8-5V7zm0 2.8V17h16V9.8l-8 5z"/></svg>info@rmiotmail.com</li>
      <li><svg viewBox="0 0 24 24" fill="none" stroke="#fff" stroke-width="2"><circle cx="12" cy="12" r="9"/><path d="M3 12h18M12 3c3 3 3 15 0 18M12 3c-3 3-3 15 0 18"/></svg>www.plonaxhub.net</li>
    </ul>
    <p class="address">87, Harbor Works Avenue<br>30918, Northland</p>
  </section>
</main>
</body>
</html>
```